Design and Renovation Company Luxury Business Card

I want to create a luxury business card for a Design and Renovation Firm . We will use our current logo. The company name is 528BUILDA. We do not want anything standard. We need a very unique concept.
Please see uploaded inspiration. I really like the textured paper option. I would like the card to be thick with debossing, and/or embossing options. The logo has orange in it but I would like to see the card with and without the orange. I think the orange may make the company feel less high-end. The goal is to elevate the logo not match its vibe per se of the logo. We want something very unique, not standard at all!
I would like a space for :
Logo,
Name,
Position,
Email,
Office number,
Website Address,
Business Address,
Thank you!
Have fun!
Target Market(s)
Home owners Age 35 +
Industry/Entity Type
Design and Renovation
Contact Information for Business Card
Logo, Name, Position, Email, Office number, Website Address, Business Address,.
Colors
Designer to choose colors to be used in the design.
Requirements
Must have
- A luxury designer feel. Must be black or dark grey but open to other luxury ideas.
Nice to have
- Gold, silver, black embossing or debossing. Textured paper design.
Should not have
- A cheap look and feel.

```html
<!DOCTYPE html>
<html lang="en">
<head>
<meta charset="utf-8">
<title>528BUILDA Business Card</title>
<link href="https://fonts.googleapis.com/css2?family=Lato:wght@400;700&display=swap" rel="stylesheet">
<style>
  :root {
    --bg: #3a3a3a;
    --card: #1e1e1e;
    --card-back: #202020;
    --deboss: #151515;
    --white: #ffffff;
    --orange: #f29a1f;
    --grey-text: #e6e6e6;
  }
  * { margin: 0; padding: 0; box-sizing: border-box; }
  html, body { width: 1200px; height: 689px; overflow: hidden; }
  body {
    background: var(--bg);
    font-family: "Lato", sans-serif;
    display: flex;
    align-items: center;
    justify-content: center;
    gap: 48px;
  }
  .card {
    width: 540px;
    height: 309px;
    border-radius: 16px;
    position: relative;
    overflow: hidden;
  }
  .company-name {
    font-weight: 700;
    font-size: 44px;
    letter-spacing: 0;
    line-height: 1;
  }

  .card--back {
    background: var(--card-back);
    display: flex;
    align-items: center;
    justify-content: center;
  }
  .card--back .company-name { color: var(--deboss); }

  .card--front { background: var(--card); color: var(--white); }
  .card--front .company-name {
    position: absolute;
    left: 40px;
    top: 48px;
    color: var(--white);
  }

  .person {
    position: absolute;
    left: 40px;
    top: 168px;
    width: 200px;
    text-align: right;
  }
  .person__name {
    color: var(--orange);
    font-size: 22px;
    font-weight: 400;
    letter-spacing: 0.5px;
  }
  .person__role {
    font-size: 15px;
    margin-top: 4px;
  }
  .divider {
    position: absolute;
    left: 258px;
    top: 160px;
    width: 1px;
    height: 70px;
    background: var(--orange);
  }
  .contacts {
    position: absolute;
    left: 276px;
    top: 160px;
    list-style: none;
  }
  .contacts li {
    display: flex;
    align-items: center;
    gap: 9px;
    font-size: 14px;
    color: var(--grey-text);
    height: 23px;
  }
  .contacts svg { width: 14px; height: 14px; flex: none; }
  .address {
    position: absolute;
    left: 40px;
    right: 40px;
    bottom: 28px;
    font-size: 14px;
    color: var(--grey-text);
    text-align: center;
  }
</style>
</head>
<body>
  <section class="card card--back" aria-label="Card back">
    <p class="company-name">528BUILDA</p>
  </section>

  <section class="card card--front" aria-label="Card front">
    <p class="company-name">528BUILDA</p>

    <div class="person">
      <p class="person__name">MARCUS HALE</p>
      <p class="person__role">Owner</p>
    </div>

    <span class="divider"></span>

    <ul class="contacts">
      <li>
        <svg viewBox="0 0 24 24" aria-hidden="true"><path fill="#f29a1f" d="M6.6 10.8a15.1 15.1 0 0 0 6.6 6.6l2.2-2.2c.3-.3.7-.4 1-.2 1.1.4 2.3.6 3.6.6.6 0 1 .4 1 1V20c0 .6-.4 1-1 1A17 17 0 0 1 3 4c0-.6.4-1 1-1h3.5c.6 0 1 .4 1 1 0 1.3.2 2.5.6 3.6.1.3 0 .7-.2 1z"/></svg>
        021-555 018 234
      </li>
      <li>
        <svg viewBox="0 0 24 24" aria-hidden="true"><rect x="2" y="5" width="20" height="14" rx="1" fill="#f29a1f"/><path d="M3 6l9 7 9-7" fill="none" stroke="#1e1e1e" stroke-width="2"/></svg>
        hello@528builda.com
      </li>
      <li>
        <svg viewBox="0 0 24 24" aria-hidden="true"><circle cx="12" cy="12" r="10" fill="#f29a1f"/><path d="M2 12h20M12 2c3 3 3 17 0 20M12 2c-3 3-3 17 0 20" fill="none" stroke="#1e1e1e" stroke-width="1.5"/></svg>
        www.528builda.com
      </li>
    </ul>

    <p class="address">87, Harbour Lane Studio 20714, Northvale</p>
  </section>
</body>
</html>
```